BOLD & MINIMALIST DESIGN NEEDED

We want a very bold but minimalistic business card design that is impactful and utilizes both sides of the business card. Our current logo is included for your use.

We want bold fonts and good use of negative space. We don't want the logo to overpower the design.

Target Market(s)

Professionals who are building new commercial buildings.

Industry/Entity Type

Construction

Contact Information for Business Card

Name, Title, email, office phone, cell phone, website

Font styles to use
Serif
Sans Serif

Requirements
Must have
• Bold design!

```html
<!DOCTYPE html>
<html lang="en">
<head>
<meta charset="utf-8">
<title>Crestmark Build – Business Card</title>
<link rel="stylesheet" href="https://fonts.googleapis.com/css2?family=Rubik:wght@500;700;900&family=Roboto:wght@400&display=swap">
<style>
  :root {
    --backdrop: #9dcc66;
    --paper: #f2efea;
    --ink: #111111;
    --card-dark: #121212;
    --accent: #7dc142;
    --body-text: #555555;
    --white: #ffffff;
  }
  * { margin: 0; padding: 0; box-sizing: border-box; }
  html, body { width: 1200px; height: 1200px; overflow: hidden; }
  body { background: var(--backdrop); position: relative; font-family: "Roboto", sans-serif; }

  .card { position: absolute; width: 686px; height: 392px; }
  .card--front { left: 261px; top: 165px; background: var(--paper); }
  .card--back { left: 262px; top: 653px; background: var(--card-dark); }

  .wordmark { position: absolute; display: flex; align-items: center; gap: 12px;
    font-family: "Rubik", sans-serif; font-weight: 900; text-transform: uppercase; letter-spacing: 1px; }
  .wordmark__square { display: block; background: var(--accent); }
  .card--front .wordmark { left: 61px; top: 132px; font-size: 34px; color: var(--ink); }
  .card--front .wordmark__square { width: 26px; height: 26px; }
  .card--back .wordmark { left: 0; right: 0; top: 168px; justify-content: center; font-size: 50px; color: var(--white); gap: 16px; }
  .card--back .wordmark__square { width: 38px; height: 38px; }

  .tab { position: absolute; left: 0; top: 220px; width: 15px; height: 41px; background: var(--accent); }
  .person { position: absolute; left: 62px; top: 220px; font-family: "Rubik", sans-serif; }
  .person__name { font-size: 21px; font-weight: 500; color: var(--accent); letter-spacing: 0.3px; line-height: 1.2; }
  .person__title { font-size: 14px; font-weight: 700; color: var(--ink); margin-top: 2px; }

  .contact { position: absolute; left: 430px; top: 223px; font-size: 15px; color: var(--body-text); line-height: 19px; }
  .contact__address { margin-bottom: 19px; }
  .contact__list { list-style: none; }
  .contact__item { display: flex; align-items: center; gap: 10px; }
  .contact__icon { width: 13px; height: 13px; flex: none; }

  .website { position: absolute; left: 0; right: 0; top: 350px; text-align: center;
    font-size: 16px; letter-spacing: 5px; color: var(--accent); }
</style>
</head>
<body>
  <section class="card card--front">
    <div class="wordmark"><span class="wordmark__square"></span>Crestmark Build</div>
    <span class="tab"></span>
    <div class="person">
      <p class="person__name">Daniel Reyes</p>
      <p class="person__title">President</p>
    </div>
    <div class="contact">
      <p class="contact__address">412 Birchwood Road<br>Fairbanks, Alaska 99701</p>
      <ul class="contact__list">
        <li class="contact__item">
          <svg class="contact__icon" viewBox="0 0 16 16"><path fill="#7dc142" d="M3.5 1l2.5 3-1.5 2c1 2 3 4 5 5l2-1.5 3 2.5-1.5 2.5C8 15 1 8 1.2 2.5z"/></svg>
          555-214-7730
        </li>
        <li class="contact__item">
          <svg class="contact__icon" viewBox="0 0 16 16"><rect x="1" y="3" width="14" height="10" fill="#7dc142"/><path d="M1.5 3.5L8 9l6.5-5.5" stroke="#f2efea" stroke-width="1.3" fill="none"/></svg>
          info@crestmarkbuild.com
        </li>
        <li class="contact__item">
          <svg class="contact__icon" viewBox="0 0 16 16"><circle cx="8" cy="8" r="7" fill="#7dc142"/><path d="M4 4.5c2 0 2 2 4 2s1 3-1 3-1 2-1 3M10 3c0 2 2 2 3 3" stroke="#f2efea" stroke-width="1.3" fill="none"/></svg>
          www.crestmarkbuild.com
        </li>
      </ul>
    </div>
  </section>

  <section class="card card--back">
    <div class="wordmark"><span class="wordmark__square"></span>Crestmark Build</div>
    <p class="website">www.crestmarkbuild.com</p>
  </section>
</body>
</html>
```